Veltrane Group Business Card Design

The CEO is looking for a new trendy look for his business card.
You can stay with current branding or come up with something new/creative. It can be 3D, including Medical Office buildings. You can use our logo in a variety of colors. Please include name, title, company name, company website, email address, cell number

Target Market(s)

Real Estate Development and Construction

Industry/Entity Type

Health care real estate

Contact Information for Business Card

Rohesh Kamdar, CEO M-604.781.2249 E-roheshkamdar@veltrane.com Address:4180 Lindqvist Ave, Tampa, FL 33482 www.veltrane.com

Font styles to use
Other font styles liked:
• Be creative

Requirements
Must have
• Creative, trendy look
Nice to have
• Please go to our website to get a feel- www. veltrane.com
Should not have
• small fonts

```html
<!DOCTYPE html>
<html lang="en">
<head>
<meta charset="utf-8">
<title>Veltrane Group Business Card</title>
<link href="https://fonts.googleapis.com/css2?family=Montserrat:wght@300;400;600;800&display=swap" rel="stylesheet">
<style>
  :root {
    --backdrop: #222222;
    --card: #161616;
    --brand-red: #b31f29;
    --ink-light: #f2f2f2;
  }
  * { margin: 0; padding: 0; box-sizing: border-box; }
  html, body { width: 1200px; height: 711px; overflow: hidden; }
  body {
    background: var(--backdrop);
    font-family: "Montserrat", sans-serif;
    position: relative;
  }
  .card {
    position: absolute;
    top: 76px;
    width: 320px;
    height: 560px;
    background: var(--card);
    border-radius: 28px;
    overflow: hidden;
  }
  .card--front { left: 250px; }
  .card--back { left: 630px; }

  .front-wordmark {
    position: absolute;
    left: 50%;
    top: 50%;
    transform: translate(-50%, -50%) rotate(90deg);
    white-space: nowrap;
    font-weight: 800;
    font-size: 52px;
    letter-spacing: -1px;
    color: var(--brand-red);
  }

  .back-content {
    position: absolute;
    inset: 0;
    display: flex;
    flex-direction: column;
    align-items: center;
    padding-top: 70px;
    text-align: center;
  }
  .back-wordmark {
    font-weight: 800;
    font-size: 31px;
    letter-spacing: -0.5px;
    color: var(--brand-red);
  }
  .holder-name {
    margin-top: 42px;
    font-weight: 600;
    font-size: 19px;
    letter-spacing: 1.5px;
    text-transform: uppercase;
    color: var(--brand-red);
  }
  .holder-title {
    margin-top: 4px;
    font-weight: 300;
    font-size: 15px;
    letter-spacing: 1px;
    color: var(--ink-light);
  }
  .icon-row {
    margin-top: 26px;
    display: flex;
    align-items: center;
    gap: 8px;
  }
  .icon-row .rule {
    width: 54px;
    height: 1.5px;
    background: var(--brand-red);
  }
  .icon-badge {
    width: 26px;
    height: 26px;
    border-radius: 7px;
    background: var(--brand-red);
    display: flex;
    align-items: center;
    justify-content: center;
  }
  .contact-list {
    margin-top: 22px;
    list-style: none;
    font-weight: 300;
    font-size: 15px;
    line-height: 1.55;
    color: var(--ink-light);
  }
  .divider {
    margin-top: 16px;
    width: 220px;
    height: 1.5px;
    background: var(--brand-red);
  }
  .address {
    margin-top: 16px;
    font-style: normal;
    font-weight: 300;
    font-size: 15px;
    line-height: 1.55;
    color: var(--ink-light);
  }
</style>
</head>
<body>
  <section class="card card--front" aria-label="Card front">
    <div class="front-wordmark">Veltrane Group</div>
  </section>

  <section class="card card--back" aria-label="Card back">
    <div class="back-content">
      <div class="back-wordmark">Veltrane Group</div>
      <h1 class="holder-name">Rohesh Kamdar</h1>
      <p class="holder-title">CEO</p>

      <div class="icon-row">
        <span class="rule"></span>
        <span class="icon-badge">
          <svg width="14" height="16" viewBox="0 0 14 16" aria-hidden="true">
            <rect x="3" y="1" width="8" height="14" rx="1.5" fill="none" stroke="#fff" stroke-width="1.4"/>
            <circle cx="7" cy="12.3" r="0.9" fill="#fff"/>
          </svg>
        </span>
        <span class="icon-badge">
          <svg width="16" height="12" viewBox="0 0 16 12" aria-hidden="true">
            <rect x="1" y="1" width="14" height="10" fill="#fff"/>
            <path d="M1 1 L8 7 L15 1" fill="none" stroke="#b31f29" stroke-width="1.3"/>
          </svg>
        </span>
        <span class="icon-badge">
          <svg width="16" height="16" viewBox="0 0 16 16" aria-hidden="true">
            <circle cx="8" cy="8" r="6.5" fill="none" stroke="#fff" stroke-width="1.4"/>
            <ellipse cx="8" cy="8" rx="2.8" ry="6.5" fill="none" stroke="#fff" stroke-width="1.1"/>
            <line x1="1.5" y1="8" x2="14.5" y2="8" stroke="#fff" stroke-width="1.1"/>
          </svg>
        </span>
        <span class="rule"></span>
      </div>

      <ul class="contact-list">
        <li>604.781.2249</li>
        <li>roheshkamdar@veltrane.com</li>
        <li>www.veltrane.com</li>
      </ul>

      <div class="divider"></div>

      <address class="address">
        4180 Lindqvist Ave,<br>
        Tampa, FL 33482
      </address>
    </div>
  </section>
</body>
</html>
```